Meridian Vault Data Works Needs a Website Desing

We need a website design for a new company based in Kuwait called Meridian Vault Data Works (MVDW). We provide Software as a Service (SaaS) solutions for small and medium business companies. We will develop the required E-systems like HR,Payroll,Accounting Systems for those customers who wants to focus on their business instead of wasting time to automate it. MVDW need a web site that represent this activity and showing our cloud products and allow out customers to easily identify their needs. as a normal web site basic things need to be included like :
about MVDW
Solutions
PressRoom
Contact us
please i need something similar to tralvex.com or ozk.com or www.plorvane.com with blue and black theme .. please check the Company's logo
hi all ,,,
the project is only design without any codes
Reason: The project is focus on design only ,, i will be really appreciated to have more designs

```html
<!DOCTYPE html>
<html lang="en">
<head>
<meta charset="utf-8">
<title>Meridian Vault Data Works</title>
<link href="https://fonts.googleapis.com/css2?family=Ubuntu:ital,wght@0,300;0,400;0,500;0,700;1,400&display=swap" rel="stylesheet">
<style>
:root{
  --blue:#2a93d5;
  --blue-light:#5aaee0;
  --link:#1a8ac6;
  --ink:#1b1b1b;
  --text:#4a4a4a;
  --muted:#7a7a7a;
  --header-bg:#f7f7f7;
  --panel:#efefef;
  --line:#dedede;
  --red:#e0474c;
  --white:#ffffff;
}
*{box-sizing:border-box;margin:0;padding:0}
html,body{width:1200px;height:1150px;overflow:hidden;background:var(--white)}
body{position:relative;font-family:"Ubuntu",sans-serif;color:var(--text)}
a{color:inherit;text-decoration:none}
.abs{position:absolute}

/* header */
.site-header{position:absolute;left:0;top:0;width:1200px;height:134px;background:var(--header-bg);border-top:4px solid var(--blue-light)}
.utility-tab{position:absolute;left:645px;top:0;width:425px;height:45px}
.utility-links{position:absolute;left:677px;top:14px;font-size:12px;font-weight:500;color:var(--white);display:flex;gap:10px;align-items:center}
.search-box{position:absolute;left:887px;top:11px;width:151px;height:20px;background:var(--white);border-radius:2px}
.search-icon{position:absolute;right:4px;top:2px}
.brand{position:absolute;left:130px;top:52px;display:flex;align-items:center;gap:12px}
.brand-mark{width:66px;height:66px;border-radius:50%;background:var(--blue)}
.brand-name{font-size:56px;font-weight:700;color:var(--ink);letter-spacing:-1px;line-height:1}
.main-nav{position:absolute;left:541px;top:94px;display:flex;align-items:center;font-size:14px;color:#333;letter-spacing:.3px}
.main-nav a{display:block;height:28px;line-height:28px}
.main-nav .active{background:var(--blue);color:var(--white);border-radius:3px;padding:0 8px;width:57px}
.main-nav .sep{margin:0 22px;color:#444}

/* hero */
.hero{position:absolute;left:0;top:134px;width:1200px;height:358px;
  background:linear-gradient(90deg,#6f88a7 0%,#a3b6ca 28%,#d1dce6 52%,#b9c6d3 66%,#4d5a6c 82%,#2b3442 100%)}
.hero-title{position:absolute;left:131px;top:102px;font-size:45px;font-weight:500;line-height:54px;color:#111;text-shadow:0 1px 1px rgba(255,255,255,.35)}
.slider-dots{position:absolute;left:130px;top:324px;display:flex;gap:12px}
.slider-dots span{display:block;width:33px;height:5px;background:var(--white)}
.slider-dots .current{background:var(--blue-light)}

/* press bar */
.press-bar{position:absolute;left:130px;top:508px;width:940px;height:59px;border:1px solid var(--line);background:#f4f4f4;box-shadow:inset 0 0 0 3px var(--white),0 3px 6px rgba(0,0,0,.06)}
.press-label{position:absolute;left:19px;top:20px;font-size:15px;font-weight:500;color:var(--ink);letter-spacing:.3px}
.press-text{position:absolute;left:128px;top:23px;font-size:12.5px;color:var(--link)}
.press-date{position:absolute;left:764px;top:23px;font-size:12px;font-style:italic;color:#444}
.press-arrow{position:absolute;top:19px;width:17px;height:22px;border:1px solid #ccc;background:var(--white)}

/* columns */
.col-title{position:absolute;top:604px;font-size:24px;font-weight:300;color:var(--ink);letter-spacing:.4px}
.col-title em{font-style:normal;color:var(--blue)}
.col-body{position:absolute;font-size:12.5px;line-height:20px;color:var(--text)}
.divider{position:absolute;top:620px;width:1px;height:250px;background:#e8e8e8}
.lead-link{font-style:italic;color:var(--link);font-size:12.5px;line-height:17px}
.read-more{position:absolute;top:858px;font-size:16px;color:#333;letter-spacing:.3px}
.solution-list{list-style:none;position:absolute;left:462px;top:697px;font-size:12.5px;color:#444}
.solution-list li{height:29px;display:flex;align-items:flex-start;gap:9px}
.bullet{width:11px;height:11px;border-radius:50%;background:var(--red);position:relative;margin-top:3px;flex:none}
.bullet::after{content:"";position:absolute;left:3px;top:3px;width:3px;height:3px;border-right:1.5px solid #fff;border-top:1.5px solid #fff;transform:rotate(45deg)}
.field{position:absolute;left:793px;width:254px;height:34px;border:1px solid #cfcfcf;border-radius:3px;background:linear-gradient(#fafafa,#f0f0f0);font-size:12px;font-style:italic;color:#888;padding:10px 13px}
.signup-btn{position:absolute;left:974px;top:827px;width:73px;height:27px;background:var(--blue);border-radius:3px;color:var(--white);font-size:12px;font-weight:500;text-align:center;line-height:27px}

/* footer */
.footer-panel{position:absolute;left:130px;top:904px;width:940px;height:187px;background:var(--panel);border-radius:3px}
.footer-col{position:absolute;top:18px}
.footer-col h4{font-size:15px;font-weight:500;color:#333;margin-bottom:7px;letter-spacing:.3px}
.footer-col ul{list-style:none}
.footer-col li{height:27px;font-size:13px;color:var(--link);display:flex;align-items:center;gap:13px}
.footer-col li::before{content:"";width:4px;height:4px;border-right:1.2px solid #333;border-top:1.2px solid #333;transform:rotate(45deg)}
.copyright{position:absolute;left:130px;top:1109px;font-size:11px;color:var(--muted)}
.copyright span{color:var(--link)}
.social{position:absolute;left:862px;top:1112px;display:flex;align-items:center;gap:12px}
.social i{display:block;width:14px;height:14px;border-radius:50%;background:#a9a9a9}
.social .rss-label{font-size:9px;color:#999;letter-spacing:1px;border-left:1px dotted #bbb;padding-left:8px}
</style>
</head>
<body>

<header class="site-header">
  <svg class="utility-tab" viewBox="0 0 425 45" width="425" height="45" aria-hidden="true">
    <path d="M0 0 H425 L410 41 Q408 45 402 45 H24 Q18 45 16 41 Z" fill="var(--blue-light)"/>
  </svg>
  <div class="utility-links">
    <span>United State</span>
    <svg width="10" height="6" viewBox="0 0 10 6"><path d="M0 0h10L5 5z" fill="#fff"/></svg>
    <span style="margin:0 4px">|</span>
    <span>My Account</span>
  </div>
  <div class="search-box">
    <svg class="search-icon" width="16" height="16" viewBox="0 0 16 16"><circle cx="6" cy="6" r="4.5" fill="none" stroke="#222" stroke-width="2"/><path d="M9.5 9.5l5 5" stroke="#222" stroke-width="2.5" stroke-linecap="round"/></svg>
  </div>

  <a class="brand" href="#">
    <span class="brand-mark"></span>
    <span class="brand-name">MVDW</span>
  </a>

  <nav class="main-nav">
    <a class="active" href="#">Home</a><span class="sep">|</span>
    <a href="#">About MVDW</a><span class="sep">|</span>
    <a href="#">Solutions</a><span class="sep">|</span>
    <a href="#">Press Room</a><span class="sep">|</span>
    <a href="#">Contact us</a>
  </nav>
</header>

<section class="hero" role="img" aria-label="Photo of a businessman in a suit touching a glowing cloud icon linked to network nodes">
  <h1 class="hero-title">We are Cloud Computing<br>Company Providing<br>SaaS</h1>
  <div class="slider-dots"><span class="current"></span><span></span><span></span><span></span></div>
</section>

<div class="press-bar">
  <span class="press-label">Press Room :</span>
  <span class="press-text">Nam fermentum vestibulum purus id aliquet. Phasellus dui ante, ultricies et sollicitudin pretium, fermentum ....</span>
  <span class="press-date">April 29, 2013</span>
  <span class="press-arrow" style="left:879px"><svg width="15" height="20" viewBox="0 0 15 20"><path d="M10 4L4 10l6 6" fill="none" stroke="#222" stroke-width="2"/></svg></span>
  <span class="press-arrow" style="left:907px"><svg width="15" height="20" viewBox="0 0 15 20"><path d="M5 4l6 6-6 6" fill="none" stroke="#222" stroke-width="2"/></svg></span>
</div>

<h2 class="col-title" style="left:131px">About <em>MVDW</em></h2>
<div class="col-body" style="left:131px;top:647px;width:290px">
  <p>Vestibulum ante ipsum primis in faucibus orci luctus et ultrices posuere cubilia Curae; Ut et scelerisque ante. Donec erat purus, faucibus vitae congue vel, porttitor nec lectus. Aenean a nibh eget turpis vehicula tempus ac sed massa. Vestibulum dolor nulla, ultrices ac tincidunt sed, laoreet non est.</p>
  <p class="lead-link" style="margin-top:6px">Lorem ipsum dolor sit amet, consectetur<br>adipiscing elit..</p>
</div>
<a class="read-more" href="#" style="left:337px">Read More</a>
<div class="divider" style="left:440px"></div>

<h2 class="col-title" style="left:461px">Our <em>Solutions</em></h2>
<p class="col-body" style="left:462px;top:647px;width:290px">Ut et scelerisque ante. Donec erat purus, faucibus vitae congue vel, porttitor nec lectus.</p>
<ul class="solution-list">
  <li><span class="bullet"></span>Storage</li>
  <li><span class="bullet"></span>Backup &amp; Recovery</li>
  <li><span class="bullet"></span>Cloud Computing</li>
  <li><span class="bullet"></span>Big Data</li>
  <li><span class="bullet"></span>Security</li>
</ul>
<a class="read-more" href="#" style="left:660px">Read More</a>
<div class="divider" style="left:770px"></div>

<h2 class="col-title" style="left:791px">Newsletter <em>Signup</em></h2>
<p class="col-body" style="left:793px;top:647px;width:270px">Subscribe to our e-Newsletter today to receive the latest issue, news, stories, events<br>and more.</p>
<div class="field" style="top:724px">Enter Name</div>
<div class="field" style="top:777px">Enter Email</div>
<p class="col-body" style="left:793px;top:820px;width:170px">Your email address will not be shared with any third party.</p>
<a class="signup-btn" href="#">SIGN UP</a>

<footer>
  <div class="footer-panel">
    <div class="footer-col" style="left:26px">
      <h4>Footer Link</h4>
      <ul><li>Aenean a nibh eget</li><li>Vestibulum dolor</li><li>Etiam risus massa</li><li>Aenean a nibh eget</li><li>Vestibulum dolor</li></ul>
    </div>
    <div class="footer-col" style="left:261px">
      <h4>Footer Link</h4>
      <ul><li>Aenean a nibh eget</li><li>Vestibulum dolor</li><li>Etiam risus massa</li><li>Aenean a nibh eget</li><li>Vestibulum dolor</li></ul>
    </div>
    <div class="footer-col" style="left:497px">
      <h4>Footer Link</h4>
      <ul><li>Aenean a nibh eget</li><li>Vestibulum dolor</li><li>Etiam risus massa</li><li>Aenean a nibh eget</li><li>Vestibulum dolor</li></ul>
    </div>
    <div class="footer-col" style="left:732px">
      <h4>Footer Link</h4>
      <ul><li>Aenean a nibh eget</li><li>Vestibulum dolor</li><li>Etiam risus massa</li><li>Aenean a nibh eget</li><li>Vestibulum dolor</li></ul>
    </div>
  </div>
  <p class="copyright">Copyright © 2013 <span>MVDW</span>. All rights reserved</p>
  <div class="social">
    <i></i><i></i><i></i><i></i><i></i>
    <span class="rss-label">RSS</span>
    <svg width="14" height="14" viewBox="0 0 14 14"><circle cx="2.5" cy="11.5" r="2" fill="#a9a9a9"/><path d="M1 6a7 7 0 0 1 7 7M1 1a12 12 0 0 1 12 12" fill="none" stroke="#a9a9a9" stroke-width="2"/></svg>
  </div>
</footer>

</body>
</html>
```